Carwash Signage

We own and operate a 25m tunnel car wash in the uk. We are looking to upgrade our signage to include the following:-

Wash selection Board Size-1300x1300mm
Conditions 1300x1300mm
Instructions 1300x1300mm
Banner 2600x600mm
Stamp card flyer a5 double sided - 9 squares for stamping 3rd square needs to say free air freshener 9th square needs to say free vip car wash.

I have attached some notes for the details that are required to be included.

We are looking for a modern smart look more European car wash style than American car wash style. It should be bold and clear. with yellow/orange & blue/green,grey colours

The final design must be in a industry standard printable format.

UPDATED BRIEF AS DISCUSSED: We require design for 2 x window decals, flag design and 50% off voucher. Attached are rough layout drawings of what they should look like - we expect the designs to be in keeping with the previous designs colours, etc that have been carried out. We Look forward to hearing from you.

Target Market(s)

local car owners within a 15-20 mile radius

Colors
0054AA
0677BA
7BADD7
CADEEF
E8F1F8
0094D4
00A9DD
6FCCEA
C7EBF8
E9F6FB
00AB8E
00BBA5
67D7C9
C6EFE9
E9F9F6

Requirements
Must have
• must be sharp and modern European look

```html
<!DOCTYPE html>
<html lang="en">
<head>
<meta charset="utf-8">
<title>Sunridge Car Wash – Wash Options</title>
<link href="https://fonts.googleapis.com/css2?family=Bebas+Neue&family=Caveat+Brush&display=swap" rel="stylesheet">
<style>
  :root{
    --blue:#0a27c4;
    --black:#000;
    --white:#fff;
    --platinum-bg:#e3e3e3;
    --silver-bg:#e6e6e6;
    --gold-bg:#f6d48a;
    --bronze-bg:#fbab7a;
    --mark-grey:#7b7b7b;
    --mark-gold:#7a4a10;
    --mark-bronze:#6d3220;
    --price-gold:#f3cc7e;
    --price-bronze:#f8a872;
    --disc-silver:#cfcfcf;
    --disc-gold:#d8ac55;
    --disc-bronze:#d38c68;
  }
  *{box-sizing:border-box;margin:0;padding:0}
  html,body{width:1200px;height:1200px;overflow:hidden;background:var(--white)}
  .board{
    width:1200px;height:1200px;display:grid;
    grid-template-columns:160px 118px 93px 82px 110px 104px 86px 79px 102px 65px 90px 111px;
    grid-template-rows:230px 191px 194px 195px 195px 195px;
    font-family:"Bebas Neue",Impact,sans-serif;
  }
  .cell{display:flex;align-items:center;justify-content:center;text-align:center;
    border-right:1px solid rgba(255,255,255,.85);border-bottom:1px solid rgba(255,255,255,.85)}
  .head{background:var(--blue);color:var(--white);font-size:25px;line-height:1;flex-direction:column}
  .head .rule{width:18px;height:1px;background:var(--white);margin:6px 0}
  .brand-cell{background:var(--black);color:var(--white);flex-direction:column;gap:6px;padding:0 8px}
  .brand{display:flex;align-items:center;gap:6px;font-size:21px;letter-spacing:.5px;white-space:nowrap}
  .brand .dot{width:14px;height:14px;border:2px solid var(--white);border-radius:50%;flex:none}
  .options-title{font-size:46px;letter-spacing:1px;line-height:1}
  .price-head{background:var(--black);color:var(--white);font-size:46px}
  .price{background:var(--black);font-size:44px;color:var(--white)}
  .price.gold{color:var(--price-gold)}
  .price.bronze{color:var(--price-bronze)}
  .row-platinum{background:var(--platinum-bg);color:var(--mark-grey)}
  .row-gold{background:var(--gold-bg);color:var(--mark-gold)}
  .row-silver{background:var(--silver-bg);color:var(--mark-grey)}
  .row-bronze{background:var(--bronze-bg);color:var(--mark-bronze)}
  .mark{width:40px;height:46px}
  .tier{width:142px;height:142px;border-radius:50%;display:flex;align-items:center;justify-content:center;
    flex-direction:column;line-height:.9}
  .tier-platinum,.tier-silver{background:var(--disc-silver);color:#6f6f6f}
  .tier-gold{background:var(--disc-gold);color:#5a380c}
  .tier-bronze{background:var(--disc-bronze);color:#4e2314}
  .tier-platinum .l1{font-size:46px}
  .tier-platinum .l2{font-size:30px}
  .tier-gold span,.tier-silver span{font-size:44px}
  .tier-bronze span{font-size:40px}
  .offers-label{background:var(--black);color:var(--white);font-size:64px;border-bottom:none}
  .offer{background:var(--blue);color:var(--white);flex-direction:column;border-bottom:none}
  .offer-pack{grid-column:2 / 7}
  .offer-loyalty{grid-column:7 / 13;border-right:none}
  .script{font-family:"Caveat Brush",cursive;font-size:52px;line-height:1}
  .offer-big{font-size:66px;line-height:1;margin-top:4px}
  .offer-price{font-size:44px;line-height:1}
  .offer-mid{font-size:60px;line-height:1}
  .offer-note{font-size:46px;line-height:1.1}
</style>
</head>
<body>
<svg width="0" height="0" style="position:absolute">
  <symbol id="asterisk" viewBox="0 0 40 46">
    <g fill="currentColor">
      <rect x="15.5" y="0" width="9" height="46" rx="1"/>
      <rect x="15.5" y="0" width="9" height="46" rx="1" transform="rotate(60 20 23)"/>
      <rect x="15.5" y="0" width="9" height="46" rx="1" transform="rotate(-60 20 23)"/>
    </g>
  </symbol>
</svg>

<main class="board">
  <div class="cell brand-cell">
    <div class="brand"><span class="dot"></span>Sunridge Car Wash</div>
    <div class="options-title">Options</div>
  </div>
  <div class="cell head">Roof<br>Brush<span class="rule"></span>6 Contour<br>Brushes<span class="rule"></span>Sill<br>Brushes</div>
  <div class="cell head">Drying<br>Double<br>Contour</div>
  <div class="cell head">Waxing</div>
  <div class="cell head">Hand<br>Brush<br>Prepared</div>
  <div class="cell head">Active<br>Foam<br>Pre Soak</div>
  <div class="cell head">Alloy<br>Wheel<br>Spray</div>
  <div class="cell head">Jade<br>Ultra<br>Wax</div>
  <div class="cell head">Jet<br>Wash<br>Pre Wash</div>
  <div class="cell head">Under<br>Body<br>Wash</div>
  <div class="cell head">Snow<br>Foam<br>Prewash</div>
  <div class="cell price-head">Price</div>

  <div class="cell row-platinum"><div class="tier tier-platinum" role="img" aria-label="VIP Platinum medallion"><span class="l1">VIP</span><span class="l2">Platinum</span></div></div>
  <div class="cell row-platinum"><svg class="mark"><use href="#asterisk"/></svg></div>
  <div class="cell row-platinum"><svg class="mark"><use href="#asterisk"/></svg></div>
  <div class="cell row-platinum"><svg class="mark"><use href="#asterisk"/></svg></div>
  <div class="cell row-platinum"><svg class="mark"><use href="#asterisk"/></svg></div>
  <div class="cell row-platinum"><svg class="mark"><use href="#asterisk"/></svg></div>
  <div class="cell row-platinum"><svg class="mark"><use href="#asterisk"/></svg></div>
  <div class="cell row-platinum"><svg class="mark"><use href="#asterisk"/></svg></div>
  <div class="cell row-platinum"><svg class="mark"><use href="#asterisk"/></svg></div>
  <div class="cell row-platinum"><svg class="mark"><use href="#asterisk"/></svg></div>
  <div class="cell row-platinum"><svg class="mark"><use href="#asterisk"/></svg></div>
  <div class="cell price">£10.00</div>

  <div class="cell row-gold"><div class="tier tier-gold" role="img" aria-label="Gold medallion"><span>Gold</span></div></div>
  <div class="cell row-gold"><svg class="mark"><use href="#asterisk"/></svg></div>
  <div class="cell row-gold"><svg class="mark"><use href="#asterisk"/></svg></div>
  <div class="cell row-gold"><svg class="mark"><use href="#asterisk"/></svg></div>
  <div class="cell row-gold"><svg class="mark"><use href="#asterisk"/></svg></div>
  <div class="cell row-gold"><svg class="mark"><use href="#asterisk"/></svg></div>
  <div class="cell row-gold"><svg class="mark"><use href="#asterisk"/></svg></div>
  <div class="cell row-gold"><svg class="mark"><use href="#asterisk"/></svg></div>
  <div class="cell row-gold"><svg class="mark"><use href="#asterisk"/></svg></div>
  <div class="cell row-gold"></div>
  <div class="cell row-gold"></div>
  <div class="cell price gold">£8.50</div>

  <div class="cell row-silver"><div class="tier tier-silver" role="img" aria-label="Silver medallion"><span>Silver</span></div></div>
  <div class="cell row-silver"><svg class="mark"><use href="#asterisk"/></svg></div>
  <div class="cell row-silver"><svg class="mark"><use href="#asterisk"/></svg></div>
  <div class="cell row-silver"><svg class="mark"><use href="#asterisk"/></svg></div>
  <div class="cell row-silver"><svg class="mark"><use href="#asterisk"/></svg></div>
  <div class="cell row-silver"><svg class="mark"><use href="#asterisk"/></svg></div>
  <div class="cell row-silver"></div>
  <div class="cell row-silver"></div>
  <div class="cell row-silver"></div>
  <div class="cell row-silver"></div>
  <div class="cell row-silver"></div>
  <div class="cell price">£7.50</div>

  <div class="cell row-bronze"><div class="tier tier-bronze" role="img" aria-label="Bronze medallion"><span>Bronze</span></div></div>
  <div class="cell row-bronze"><svg class="mark"><use href="#asterisk"/></svg></div>
  <div class="cell row-bronze"><svg class="mark"><use href="#asterisk"/></svg></div>
  <div class="cell row-bronze"><svg class="mark"><use href="#asterisk"/></svg></div>
  <div class="cell row-bronze"><svg class="mark"><use href="#asterisk"/></svg></div>
  <div class="cell row-bronze"></div>
  <div class="cell row-bronze"></div>
  <div class="cell row-bronze"></div>
  <div class="cell row-bronze"></div>
  <div class="cell row-bronze"></div>
  <div class="cell row-bronze"></div>
  <div class="cell price bronze">£6.50</div>

  <div class="cell offers-label">Offers</div>
  <div class="cell offer offer-pack">
    <div class="script">VIP Platinum Wash Pack</div>
    <div class="offer-big">Buy 2 Get 1 Free</div>
    <div class="offer-price">£20.00</div>
  </div>
  <div class="cell offer offer-loyalty">
    <div class="script">Loyalty Card Available</div>
    <div class="offer-mid">Wash + Earn</div>
    <div class="offer-note">Ask the operator for details</div>
  </div>
</main>
</body>
</html>
```